Poster announcing University Web Analytics talk

We need a poster to announce an upcoming talk on Web Analytics at the local University. The event is addressed to final year students (mostly in Informatic Engineering, although other majors are wellcomed as well) who may be interested in specializing in this rising field.

The poster should present a brief list of the points we'll be addressing, as well as the place and time of the meeting. Also, it must feature our company logo (check the uploads section to find it) and our website url: http://www.brasslanternworks.net.

Texts for the poster:

Headline: "Get specialized in Web & Mobile Analytics"

Topics that will be covered:
- Introduction to Analytics, market, work opportunities
- Know the basics of an Analytics project: planning, phases, implementation
- Job bank: bring your CV!

Event information: "Thursday 20th June at the Facultad de Cartografía, Universidad de Valdemora". [A space to fill with the time must be provided here]

However, we'll be translating all the text to Spanish later, so we'll need a file where we can modify the text layers.
Updates

Thanks to all of you, we're receiving so many excellent works!

We had missed to include some important information on the brief - we didn't say anything about the colors, and we have been getting some designs based in dark colors. Now, it doesn't matter what colors you use, but we'd like better a brighter design (no matter if the color combination is more playful or either rather serious). This is going to be a free talk addressed to last year students, so we want to transmit a feeling of an interesting, easy and entertaining afternoon.

I hope these comments are helpful, please reach me with any question or comment. 

Thanks a lot again!
Nuria 
BL team

Target Market(s)

Final year students and graduates.

Industry/Entity Type

Bank

Requirements
Must have
• Design must be submitted in vector format, preferably .psd. We must be able to modify the text layers. Our logo (check the files section) and website url (http://www.brasslanternworks.net) must be included
Nice to have
• Illustrations making reference to Analytics (charts, statistics, code) and/or the internet will be a plus!

```html
<!DOCTYPE html>
<html lang="en">
<head>
<meta charset="utf-8">
<title>Get specialized in Web &amp; Mobile Analytics</title>
<link rel="stylesheet" href="https://fonts.googleapis.com/css2?family=Roboto+Condensed:wght@400;700&family=Roboto:wght@700&display=swap">
<style>
  :root {
    --bg-side: #e4e5e8;
    --bg-panel: #f2f2f3;
    --text-grey: #6b6b6b;
    --text-dark: #5a5a5a;
    --white: #ffffff;
    --blue: #2f6fc4;
    --blue-dark: #1f4f9a;
    --navy: #243b7c;
    --navy-dark: #172757;
    --green-dark: #2b7d3b;
    --green-dark-shade: #1c5a28;
    --green: #4aaa48;
    --green-shade: #33842f;
    --charcoal: #3d3d3f;
    --charcoal-shade: #262628;
    --brand: #2b6f8a;
  }
  html, body { margin: 0; padding: 0; overflow: hidden; }
  body { width: 849px; height: 1200px; }
  .poster {
    position: relative;
    width: 849px;
    height: 1200px;
    overflow: hidden;
    background: linear-gradient(90deg, var(--bg-side) 0, var(--bg-side) 265px, var(--bg-panel) 265px, #f6f6f7 100%);
    font-family: "Roboto Condensed", "Arial Narrow", sans-serif;
  }
  .illustration {
    position: absolute;
    left: 0; top: 0;
    width: 290px; height: 1150px;
    background:
      radial-gradient(circle at 40% 12%, rgba(214,60,50,.85) 0, rgba(214,60,50,0) 38%),
      radial-gradient(circle at 30% 55%, rgba(40,140,210,.85) 0, rgba(40,140,210,0) 40%),
      radial-gradient(circle at 70% 35%, rgba(245,170,40,.85) 0, rgba(245,170,40,0) 35%),
      radial-gradient(circle at 45% 80%, rgba(240,130,40,.7) 0, rgba(240,130,40,0) 35%),
      linear-gradient(180deg, #f0d6cf 0%, #cfe0ef 45%, #e8dcc8 80%, rgba(228,229,232,0) 100%);
    -webkit-mask-image: linear-gradient(90deg, #000 75%, transparent 100%);
            mask-image: linear-gradient(90deg, #000 75%, transparent 100%);
  }
  .headline {
    position: absolute;
    left: 303px; top: 172px;
    margin: 0;
    font-weight: 700;
    font-size: 45px;
    line-height: 50px;
    color: var(--text-grey);
    letter-spacing: -0.3px;
  }
  .topics { position: absolute; left: 0; top: 0; width: 849px; height: 1200px; }
  .topic-label {
    position: absolute;
    margin: 0;
    color: var(--white);
    font-family: "Roboto", "Arial", sans-serif;
    font-weight: 700;
    font-size: 17px;
    line-height: 22px;
  }
  .topic-label.intro { left: 310px; top: 320px; }
  .topic-label.basics { left: 303px; top: 430px; }
  .topic-label.planning { left: 303px; top: 502px; }
  .topic-label.jobs { left: 303px; top: 584px; }
  .topic-label.cv {
    left: 303px; top: 664px;
    font-family: "Roboto Condensed", "Arial Narrow", sans-serif;
    font-size: 32px; line-height: 40px;
  }
  .event {
    position: absolute;
    left: 303px; top: 792px;
    margin: 0;
    font-weight: 700;
    font-size: 22px;
    line-height: 28px;
    color: var(--text-dark);
  }
  .brand {
    position: absolute;
    left: 303px; top: 912px;
    display: flex; align-items: center; gap: 14px;
  }
  .brand-mark { width: 48px; height: 48px; background: var(--brand); }
  .brand-name {
    font-weight: 700;
    font-size: 34px;
    line-height: 34px;
    color: var(--brand);
    width: 200px;
  }
  .website {
    position: absolute;
    left: 303px; top: 986px;
    margin: 0;
    font-weight: 700;
    font-size: 19px;
    color: var(--text-dark);
  }
</style>
</head>
<body>
<main class="poster">
  <div class="illustration" role="img" aria-label="Collage of colourful internet browser symbols, a compass, rising bar chart and swooping arrows"></div>

  <h1 class="headline">Get specialized in<br>Web &amp; Mobile Analytics</h1>

  <svg class="topics" viewBox="0 0 849 1200" aria-hidden="true">
    <!-- topic ribbons -->
    <polygon points="278,308 680,308 705,346 680,392 265,392" fill="var(--blue)"/>
    <polygon points="265,392 290,392 290,402 265,402" fill="var(--blue-dark)"/>
    <polygon points="278,402 640,402 663,440 640,478 265,478" fill="var(--navy)"/>
    <polygon points="265,478 290,478 290,484 265,484" fill="var(--navy-dark)"/>
    <polygon points="278,478 612,478 635,516 612,554 265,554" fill="var(--green-dark)"/>
    <polygon points="265,554 290,554 290,560 265,560" fill="var(--green-dark-shade)"/>
    <polygon points="278,558 665,558 690,598 665,638 265,638" fill="var(--green)"/>
    <polygon points="265,638 290,638 290,645 265,645" fill="var(--green-shade)"/>
    <polygon points="278,645 535,645 557,687 535,730 265,730" fill="var(--charcoal)"/>
    <polygon points="265,730 290,730 290,737 265,737" fill="var(--charcoal-shade)"/>
  </svg>

  <p class="topic-label intro">Introduction to Analytics, market,<br>work opportunities</p>
  <p class="topic-label basics">Know the basics of an Analytics project</p>
  <p class="topic-label planning">Planning, phases, implementation</p>
  <p class="topic-label jobs">Job bank</p>
  <p class="topic-label cv">bring your CV!</p>

  <p class="event">Thursday 20th June at the Facultad de Cartografía.<br>Universidad de Valdemora<br>Time here</p>

  <div class="brand">
    <span class="brand-mark"></span>
    <span class="brand-name">brass lantern works</span>
  </div>

  <p class="website">www.brasslanternworks.net</p>
</main>
</body>
</html>
```